VORLE Diagnostics Pooling One Sheet

The process and concept for pooling is to target large populations of people; i.e. a school, prison, employer (where people are isolated by pods), then to test them all in one controllable group. By breaking down the pool size (ideally is 12 or 16 max) then when a positive pool pops up, the entity has the lab automatically reflex to test the whole pool to determine who is positive. During that exchange, several workflows could take place from the population that was being tested. This type of pooled testing is called Surveillance testing ,when it reflects, then it goes to Screening or Diagnostic testing.

The workflow is:
School/employer collects all patient information captured on a requisition form or electronically (w signature) and DOES NOT send to VORLE
School/employer collects individual specimens and labels them with a unique bar code (non-repeating and can include the DOB)
School/employer is responsible for housing and managing all the unique patient information for each individual specimen
School/employer delivers specimens to VORLE and School/employer directs VORLE what specimens are in what designated pool (one pool size for entire project)
When a pool is positive, VORLE notifies School/employer
When reflex testing in indicated for client, School/employer submits to VORLE on demand all patient information needed to process the reflexed option
VORLE reports back to School/employer in 12 hours the results of the retest
https://www.healthregistry-example.org/medical-devices/coronavirus-covid-19-and-medical-devices/pooled-sample-testing-and-screening-testing-covid-19
https://www.testmere.com/coronavirus-disease-covid-19/news/testmere-receives-authorization-covid-19-sample-pooling

Target Market(s)

Schools, Universities, Employers

Font styles to use
Sans Serif

Colors
85acd3
85cae6
34a6d7

Requirements
Must have
• VORLE branded along with an elegant yet clinical feel. have all contact information for VORLE Diagnostics. Go to www.vorledx.com for all info

```html
<!DOCTYPE html>
<html lang="en">
<head>
<meta charset="utf-8">
<title>VORLE Diagnostics – Pooled Sample Testing</title>
<link rel="stylesheet" href="https://fonts.googleapis.com/css2?family=Bebas+Neue&family=Montserrat:wght@300;400;500;700&display=swap">
<style>
  :root{
    --navy:#0a58a8;
    --sky:#3d8fd0;
    --covid:#0a72c2;
    --teal:#0896a3;
    --label-top:#0b60b5;
    --label-bottom:#063b86;
    --bar:#2b3e4b;
    --ink:#111a22;
    --brand:#2f7f93;
    --white:#ffffff;
  }
  *{margin:0;padding:0;box-sizing:border-box}
  html,body{width:927px;height:1200px;overflow:hidden;background:var(--white)}
  .sheet{position:relative;width:927px;height:1200px;font-family:"Montserrat",sans-serif;color:var(--ink)}
  .hero{position:absolute;left:0;top:0;width:927px;height:440px;
    background:
      radial-gradient(ellipse 420px 300px at 700px 170px,#5bb8d8 0%,#8dcfe6 45%,rgba(200,230,240,0) 80%),
      radial-gradient(ellipse 260px 220px at 140px 260px,#c9cfd4 0%,rgba(220,225,230,0) 75%),
      linear-gradient(180deg,#e9eef2 0%,#dfe8ee 55%,#ffffff 100%);
    -webkit-mask-image:linear-gradient(180deg,#000 75%,transparent 100%);
            mask-image:linear-gradient(180deg,#000 75%,transparent 100%);}
  .title{position:absolute;left:0;width:927px;text-align:center;font-family:"Bebas Neue",sans-serif;line-height:1;letter-spacing:1px}
  .title-1{top:398px;font-size:84px;padding-right:14px}
  .title-2{top:478px;font-size:84px;padding-right:14px}
  .navy{color:var(--navy)} .sky{color:var(--sky)} .covid{color:var(--covid)}
  .intro{position:absolute;left:66px;top:568px;width:820px;font-size:15.2px;font-weight:500;line-height:22.6px;color:var(--ink)}
  .workflow{position:absolute;left:0;top:765px;width:927px;height:272px;background:var(--teal)}
  .workflow-label{position:absolute;left:110px;top:747px;width:273px;height:44px;
    background:linear-gradient(180deg,var(--label-top),var(--label-bottom));
    color:var(--white);font-family:"Bebas Neue",sans-serif;font-size:34px;line-height:46px;padding-left:30px}
  .step{position:absolute;color:var(--white);font-size:13px;font-weight:300;line-height:18.2px;letter-spacing:.3px}
  .step.left{left:110px;width:330px}
  .step.right{left:531px;width:350px}
  .hex{position:absolute;width:46px;height:50px}
  .contact-bar{position:absolute;left:0;top:1037px;width:927px;height:42px;background:var(--bar);
    color:var(--white);font-weight:700;font-size:17px;letter-spacing:.4px;display:flex;align-items:center;justify-content:center;gap:10px}
  .contact-bar svg{width:24px;height:24px}
  .brand{position:absolute;left:104px;top:1114px;display:flex;align-items:center;gap:14px}
  .brand-square{width:44px;height:44px;background:var(--bar)}
  .brand-name{font-weight:700;font-size:30px;color:var(--brand);letter-spacing:.5px}
  .address{position:absolute;left:588px;top:1098px;font-size:16.5px;font-weight:500;line-height:21px}
  .address .line{padding-left:28px}
  .address svg,.email svg{position:absolute;left:0}
  .email{position:absolute;left:588px;top:1155px;font-size:16.5px;font-weight:500;padding-left:30px}
</style>
</head>
<body>
<div class="sheet">
  <div class="hero" role="img" aria-label="Clinician in blue protective gown, mask and goggles taking a throat swab from a seated older patient"></div>

  <h1 class="title title-1"><span class="navy">Pooled Sample Testing</span> <span class="sky">And</span></h1>
  <h1 class="title title-2"><span class="sky">Screening for</span> <span class="covid">COVID-19</span></h1>

  <p class="intro">The process and concept for pooling is to target large populations of people; i.e. a school, prison, employer (where people are isolated by pods), then to test them all in one controllable group. By breaking down the pool size (ideally is 12 or 16 max) then when a positive pool pops up, the entity has the lab automatically reflex to test the whole pool to determine who is positive. During that exchange, several workflows could take place from the population that was being tested. This type of pooled testing is called Surveillance testing ,when it reflects, then it goes to Screening or Diagnostic testing.</p>

  <section class="workflow"></section>
  <div class="workflow-label">The Workflow Is</div>

  <svg class="hex" style="left:35px;top:819px" viewBox="0 0 46 50"><polygon points="23,0 46,12.5 46,37.5 23,50 0,37.5 0,12.5" fill="#fff"/><path d="M15 15h14v20H15z M18 21h8 M18 25h8 M18 29h4" fill="none" stroke="#0896a3" stroke-width="1.8"/></svg>
  <svg class="hex" style="left:35px;top:885px" viewBox="0 0 46 50"><polygon points="23,0 46,12.5 46,37.5 23,50 0,37.5 0,12.5" fill="#fff"/><rect x="11" y="21" width="24" height="8" rx="4" transform="rotate(-30 23 25)" fill="none" stroke="#0896a3" stroke-width="1.8"/></svg>
  <svg class="hex" style="left:33px;top:948px" viewBox="0 0 46 50"><polygon points="23,0 46,12.5 46,37.5 23,50 0,37.5 0,12.5" fill="#fff"/><circle cx="22" cy="19" r="5" fill="none" stroke="#0896a3" stroke-width="1.8"/><path d="M13 35c1-6 5-9 9-9s8 3 9 9" fill="none" stroke="#0896a3" stroke-width="1.8"/></svg>

  <p class="step left" style="top:823px">School/employer collects all patient information captured on a requisition form or electronically (w signature) and DOES NOT send to VORLE</p>
  <p class="step left" style="top:887px">School/employer collects individual specimens and labels them with a unique bar code (non-repeating and can include the DOB)</p>
  <p class="step left" style="top:950px">School/employer is responsible for housing and managing all the unique patient information for each individual specimen</p>

  <svg class="hex" style="left:473px;top:779px" viewBox="0 0 46 50"><polygon points="23,0 46,12.5 46,37.5 23,50 0,37.5 0,12.5" fill="#fff"/><circle cx="23" cy="17" r="4" fill="none" stroke="#0896a3" stroke-width="1.8"/><rect x="14" y="25" width="18" height="11" fill="none" stroke="#0896a3" stroke-width="1.8"/><path d="M23 28v5 M20.5 30.5h5" stroke="#0896a3" stroke-width="1.6"/></svg>
  <svg class="hex" style="left:473px;top:859px" viewBox="0 0 46 50"><polygon points="23,0 46,12.5 46,37.5 23,50 0,37.5 0,12.5" fill="#fff"/><path d="M15 17c0 10 6 17 16 17l2-4-4-3-2 2c-3-1-5-3-6-6l2-2-3-4z" fill="none" stroke="#0896a3" stroke-width="1.6"/><path d="M26 14v8 M22 18h8" stroke="#0896a3" stroke-width="1.6"/></svg>
  <svg class="hex" style="left:473px;top:912px" viewBox="0 0 46 50"><polygon points="23,0 46,12.5 46,37.5 23,50 0,37.5 0,12.5" fill="#fff"/><path d="M16 16h14v18H16z M19 22h8 M19 26h8" fill="none" stroke="#0896a3" stroke-width="1.8"/></svg>
  <svg class="hex" style="left:473px;top:971px" viewBox="0 0 46 50"><polygon points="23,0 46,12.5 46,37.5 23,50 0,37.5 0,12.5" fill="#fff"/><rect x="14" y="15" width="16" height="21" fill="none" stroke="#0896a3" stroke-width="1.8"/><circle cx="29" cy="29" r="5" fill="#fff" stroke="#0896a3" stroke-width="1.6"/></svg>

  <p class="step right" style="top:785px">School/employer delivers specimens to VORLE and School/employer directs VORLE what specimens are in what designated pool (one pool size for entire project)</p>
  <p class="step right" style="top:866px">When a pool is positive, VORLE notifies School/employer</p>
  <p class="step right" style="top:919px">When reflex testing in indicated for client, School/ employer submits to VORLE on demand all patient information needed to process the reflexed option</p>
  <p class="step right" style="top:982px">VORLE reports back to School/employer in 12 hours the results of the retest</p>

  <div class="contact-bar">
    <span>FOR MORE DETAILS VISIT OR CALL</span>
    <svg viewBox="0 0 24 24" fill="none" stroke="#fff" stroke-width="1.8"><circle cx="12" cy="12" r="10"/><ellipse cx="12" cy="12" rx="4.5" ry="10"/><path d="M2 12h20"/></svg>
    <span>WWW.VORLEDX.COM</span>
    <svg viewBox="0 0 24 24" fill="none" stroke="#fff" stroke-width="1.8"><path d="M5 3c-2 9 5 17 14 17l2-4-5-3-2 2c-3-1-6-4-7-7l2-2-3-5z"/></svg>
    <span>844-555-0142</span>
  </div>

  <div class="brand">
    <div class="brand-square"></div>
    <span class="brand-name">VORLE Diagnostics</span>
  </div>

  <div class="address">
    <svg width="18" height="24" viewBox="0 0 18 24" style="top:2px"><path d="M9 1C5 1 2 4 2 8c0 5 7 12 7 12s7-7 7-12c0-4-3-7-7-7z" fill="none" stroke="#3aa6c1" stroke-width="1.8"/><circle cx="9" cy="8" r="2.5" fill="none" stroke="#3aa6c1" stroke-width="1.6"/><path d="M6 23h6" stroke="#3aa6c1" stroke-width="1.6"/></svg>
    <div class="line">1180 Meridian Park Way Suite B</div>
    <div class="line">Halden, MD 21790</div>
  </div>
  <div class="email">
    <svg width="20" height="16" viewBox="0 0 20 16" style="top:3px"><rect x="1" y="2" width="18" height="12" fill="none" stroke="#3aa6c1" stroke-width="1.8"/><path d="M5 6l5 4 5-4" fill="none" stroke="#3aa6c1" stroke-width="1.6"/></svg>
    info@vorledx.com
  </div>
</div>
</body>
</html>
```